Bring me business with this creative business card

Design my new business card. I am looking for something different with an impact. People will take a look at this card & they will 1- see how different & creative I am, 2-understand what I do 3- Call me to meet me!

I make videos with a message, testimonials. I am dynamic, fun, creative & human. My new website is in construction but in the meantime you can check this old one: brightpath.ca & another one Tidebloom.com & tidebloom facebook page.
I make videos. sometimes with a cameraman, sometimes with my phone. As an ex Public Relations agent, the message is the most important thing for me. I want to make my clients shine! When they start with me they often remind me of a lamb, when I finish coaching them they are powerful like LIONS! That's why I need a powerful business card!

Target Market(s)

Entrepreneurs, solo entrepreneurs, small & medium companies & start ups. People i will meet while networking. People that need videos on their website & social Networks to get attention, to be visible. men & women. From 35 to 49 years old.
I am an ex Public relations agent. I used to send clients in traditional medias, now with videos they have more chances to be seen on google the new media. I do videos of the president, his team, his loyal clients saying how great the company is & expert videos like series so people can be seen for example every 1 st of every month with a short 2 minute video. Also with my 20 years in marketing & communications I can coach & give tips to anybody who needs it.
Target: anybody who would like my old website brightpath.ca & I also have another website but it will be off line soon: tidebloom.com could give you ideas.

Industry/Entity Type

Communications

Contact Information for Business Card

I am in Montreal,So the business cards have to be the usual size like we have in Montreal: 9 cm x 5 cm
Details:My text: Mathilde Tessier Communication coach/Chief Lion. "Creating Videos as unique as you" off: 514-555-0147 cell: 514-555-0183. tidebloom.com
mathilde@tidebloom.com logo facebook, youtube, instagram

Colors
f37122

Requirements
Must have
• Dynamic, happy. Orange. Be creative in the look but NOT the shape of the card. Easy to read. Big enough to read.
Should not have
• No funny shapes: no round, no square, just the usual. I love creative but NOT on shape.

```html
<!DOCTYPE html>
<html lang="en">
<head>
<meta charset="utf-8">
<title>Tidebloom – Business Card</title>
<link rel="stylesheet" href="https://fonts.googleapis.com/css2?family=Roboto:wght@400;500&display=swap">
<style>
  :root {
    --backdrop: #1f1f20;
    --card: #f7f7f5;
    --orange: #f37122;
    --orange-deep: #ef5a24;
    --amber: #f6a21b;
    --yellow: #ffc928;
    --ink: #4a4a4a;
    --rule: #b9b9b9;
  }
  * { margin: 0; padding: 0; box-sizing: border-box; }
  html, body {
    width: 1200px; height: 960px; overflow: hidden;
    background: var(--backdrop);
    font-family: "Roboto", Arial, sans-serif;
  }
  .card {
    position: absolute; left: 320px; width: 600px;
    background: var(--card);
    overflow: hidden;
  }
  .card--front { top: 100px; height: 345px; }
  .card--back { top: 493px; height: 342px; }

  .emblem {
    position: absolute;
    background: radial-gradient(ellipse at 50% 55%, var(--yellow) 0%, var(--amber) 45%, var(--orange) 80%, var(--orange-deep) 100%);
    border-radius: 38% 38% 46% 46% / 30% 30% 58% 58%;
  }
  .card--front .emblem { left: 215px; top: 68px; width: 170px; height: 208px; }

  .social { position: absolute; right: 34px; top: 34px; display: flex; gap: 5px; }
  .social__dot { width: 22px; height: 22px; border-radius: 50%; background: var(--orange-deep); }
  .social__dot:last-child { background: none; border: 1.5px solid var(--orange-deep); }

  .slogan {
    position: absolute; left: 0; right: 0; top: 302px;
    text-align: center; color: var(--orange);
    font-size: 13px; font-weight: 500;
  }

  .watermark {
    position: absolute; left: -10px; top: 68px; width: 255px; height: 290px;
    background: radial-gradient(ellipse at 45% 55%, var(--yellow), var(--amber));
    border-radius: 40% 40% 48% 48% / 30% 30% 60% 60%;
    opacity: 0.18;
  }
  .card--back .emblem { left: 442px; top: 29px; width: 82px; height: 90px; }

  .holder { position: absolute; left: 32px; top: 120px; }
  .holder__name {
    color: var(--orange-deep); font-size: 22px; font-weight: 500;
    text-transform: uppercase; letter-spacing: 0.2px;
  }
  .holder__role {
    margin-top: 6px; color: var(--amber); font-size: 14px; font-weight: 400;
    text-transform: uppercase;
  }
  .divider {
    position: absolute; left: 32px; top: 174px; width: 394px; height: 1px;
    background: var(--rule);
  }
  .brand {
    position: absolute; left: 398px; top: 138px; width: 172px;
    text-align: center; color: var(--orange);
  }
  .brand__name { font-size: 27px; font-weight: 500; letter-spacing: 2px; line-height: 1; }
  .brand__tagline {
    margin-top: 8px; font-size: 9px; letter-spacing: 1px; color: var(--amber);
    display: flex; align-items: center; gap: 6px;
  }
  .brand__tagline::before, .brand__tagline::after {
    content: ""; flex: 1; height: 1px; background: var(--amber);
  }

  .contact { position: absolute; left: 32px; top: 259px; list-style: none; }
  .contact__item {
    display: flex; align-items: center; gap: 8px;
    color: var(--ink); font-size: 14px; line-height: 19.5px;
  }
  .contact__icon { width: 13px; height: 13px; fill: var(--orange-deep); flex: none; }
  .website {
    position: absolute; right: 30px; top: 298px;
    color: var(--ink); font-size: 14px;
  }
</style>
</head>
<body>
  <section class="card card--front">
    <div class="social" aria-label="Social networks">
      <span class="social__dot"></span><span class="social__dot"></span><span class="social__dot"></span>
    </div>
    <div class="emblem" role="img" aria-label="Low-poly orange lion head illustration"></div>
    <p class="slogan">Creating Videos as unique as you</p>
  </section>

  <section class="card card--back">
    <div class="watermark" role="img" aria-label="Faint large lion head decoration"></div>
    <div class="emblem" role="img" aria-label="Low-poly orange lion head illustration"></div>

    <div class="holder">
      <h1 class="holder__name">Mathilde T.</h1>
      <p class="holder__role">Communication Coach/Chief Lion</p>
    </div>
    <div class="divider"></div>

    <div class="brand">
      <div class="brand__name">TIDEBLOOM</div>
      <div class="brand__tagline">1 VIDEO 1 MESSAGE</div>
    </div>

    <ul class="contact">
      <li class="contact__item">
        <svg class="contact__icon" viewBox="0 0 24 24" aria-hidden="true"><path d="M6.6 10.8a15.1 15.1 0 0 0 6.6 6.6l2.2-2.2a1 1 0 0 1 1-.25 11.4 11.4 0 0 0 3.6.57 1 1 0 0 1 1 1V20a1 1 0 0 1-1 1A17 17 0 0 1 3 4a1 1 0 0 1 1-1h3.5a1 1 0 0 1 1 1c0 1.25.2 2.45.57 3.57a1 1 0 0 1-.25 1z"/></svg>
        514-555-0147
      </li>
      <li class="contact__item">
        <svg class="contact__icon" viewBox="0 0 24 24" aria-hidden="true"><path d="M7 1h10a2 2 0 0 1 2 2v18a2 2 0 0 1-2 2H7a2 2 0 0 1-2-2V3a2 2 0 0 1 2-2zm0 3v14h10V4zm5 15.5a1 1 0 1 0 0 2 1 1 0 0 0 0-2z"/></svg>
        514-555-0183.
      </li>
      <li class="contact__item">
        <svg class="contact__icon" viewBox="0 0 24 24" aria-hidden="true"><path d="M2 5h20v14H2zm2 2v.5l8 5 8-5V7zm0 2.8V17h16V9.8l-8 5z"/></svg>
        mathilde@tidebloom.com
      </li>
    </ul>
    <p class="website">www.tidebloom.com</p>
  </section>
</body>
</html>
```